Mobile Friendly Lead Generation Landing Page

We are a web marketing company that specialized in web lead generation. Recently we have started buying media from mobile devices and we need a mobile interface(landing page) where we can collect user data in an effective manner.

Our current mobile landing page is:
http://www.tutorpath.example.com/lp13d/index.aspx?a=true&source=841356
Through this you can see what the steps/questions users need to answer to get matched to a school. We need the design for the whole process.

We are pretty open for design ideas and our goal is to make this mobile optimized landing page have the look and feel of an app...but not an app.
There are several questions in the process but we are open to changing the way they are presented. As in, you can have one question at a time or a few.
The goal is to make this EXTREMELY EASY for users to interact with.

One example that we have liked is:
http://learnvane.example/schools/57214-page1.lvne (please note that this opens only on mobile devices)

Some of these screenshots are attached.

Our web form looks like this:
http://www.tutorpath.example.com/lp88/index.aspx?a=true

```html
<!DOCTYPE html>
<html lang="en">
<head>
<meta charset="utf-8">
<title>College Match – Main Screen</title>
<link href="https://fonts.googleapis.com/css2?family=Open+Sans:wght@400;600;700&display=swap" rel="stylesheet">
<style>
  :root {
    --page-bg: #eef3f6;
    --sky: #17a4f2;
    --sky-soft: #c2e5f8;
    --royal: #1538e0;
    --royal-deep: #1230d8;
    --ink: #1b2533;
    --row-line: #d5dbe2;
    --white: #ffffff;
  }
  * { box-sizing: border-box; margin: 0; padding: 0; }
  html, body {
    width: 800px; height: 1200px; overflow: hidden;
    background: var(--page-bg);
    font-family: "Open Sans", Arial, sans-serif;
  }
  .screen {
    position: absolute; left: 80px; top: 32px;
    width: 640px; height: 1136px;
    background: var(--white);
    display: flex; flex-direction: column;
    overflow: hidden;
    box-shadow: 0 6px 24px rgba(20, 40, 80, .15);
  }
  .status-bar {
    height: 41px; background: var(--sky); color: var(--white);
    display: flex; align-items: center; justify-content: space-between;
    padding: 0 18px; font-size: 21px;
  }
  .status-bar .carrier { display: flex; align-items: center; gap: 10px; }
  .status-bar .time { font-weight: 600; }
  .status-bar .battery { display: flex; align-items: center; gap: 8px; }
  .address-bar {
    height: 85px; background: var(--sky);
    display: flex; align-items: center; padding: 0 14px 10px;
  }
  .address-field {
    flex: 1; height: 64px; border-radius: 8px;
    background: rgba(255, 255, 255, .3);
    color: var(--white); font-size: 27px;
    display: flex; align-items: center; justify-content: center; position: relative;
  }
  .address-field svg { position: absolute; right: 14px; }
  .hero {
    height: 267px; background: var(--sky-soft);
    display: flex; flex-direction: column; align-items: center;
  }
  .ribbon { position: relative; margin-top: 24px; width: 560px; height: 110px; }
  .ribbon svg { position: absolute; left: 0; top: 0; }
  .ribbon-text {
    position: absolute; left: 80px; right: 80px; top: 8px; bottom: 8px;
    display: flex; align-items: center; justify-content: center; text-align: center;
    color: var(--white); font-size: 23px; line-height: 1.4;
  }
  .hero-title { margin-top: 36px; font-size: 36px; color: var(--ink); }
  .hero-title strong { font-weight: 700; color: #0f2a5a; }
  .interest-header {
    height: 85px; background: var(--royal); color: var(--white);
    display: flex; align-items: center; justify-content: center;
    font-size: 30px; letter-spacing: .3px;
  }
  .interest-list { list-style: none; background: var(--white); }
  .interest-item {
    height: 87px; display: flex; align-items: center; padding: 0 16px 0 14px;
    position: relative;
  }
  .interest-item::after {
    content: ""; position: absolute; left: 100px; right: 0; bottom: 0;
    height: 1px; background: var(--row-line);
  }
  .interest-icon {
    width: 70px; height: 70px; border-radius: 50%; background: var(--sky);
    display: flex; align-items: center; justify-content: center; flex: none;
  }
  .interest-label { flex: 1; margin-left: 20px; font-size: 26px; color: var(--ink); }
  .interest-go {
    width: 40px; height: 40px; border-radius: 50%; background: var(--sky);
    display: flex; align-items: center; justify-content: center;
  }
  .list-foot { flex: 1; background: var(--sky-soft); }
  .toolbar {
    height: 111px; background: var(--royal-deep);
    display: flex; align-items: center; justify-content: space-around; padding: 0 10px;
  }
</style>
</head>
<body>
<main class="screen">
  <div class="status-bar">
    <div class="carrier">
      <svg width="62" height="14" viewBox="0 0 62 14"><g fill="#fff"><circle cx="6" cy="7" r="5.5"/><circle cx="18.5" cy="7" r="5.5"/><circle cx="31" cy="7" r="5.5"/></g><g fill="none" stroke="#fff" stroke-width="1.5"><circle cx="43.5" cy="7" r="5"/><circle cx="56" cy="7" r="5"/></g></svg>
      <span>Novalink</span>
      <svg width="26" height="20" viewBox="0 0 26 20" fill="none" stroke="#fff" stroke-width="2.6" stroke-linecap="round"><path d="M2 7a16 16 0 0 1 22 0"/><path d="M6 11a10 10 0 0 1 14 0"/><circle cx="13" cy="16" r="1.8" fill="#fff" stroke="none"/></svg>
    </div>
    <span class="time">4:21 PM</span>
    <div class="battery">
      <span>100%</span>
      <svg width="46" height="20" viewBox="0 0 46 20"><rect x="1" y="1" width="40" height="18" rx="3" fill="none" stroke="#fff" stroke-width="1.6"/><rect x="3.5" y="3.5" width="35" height="13" rx="1.5" fill="#fff"/><rect x="42" y="6" width="3" height="8" rx="1" fill="#fff"/></svg>
    </div>
  </div>

  <div class="address-bar">
    <div class="address-field">
      www.tutorpath.example.com
      <svg width="34" height="34" viewBox="0 0 34 34" fill="none" stroke="#fff" stroke-width="2.2" stroke-linecap="round"><path d="M27 13a11 11 0 0 0-19-3"/><path d="M8 5v5h5"/><path d="M7 21a11 11 0 0 0 19 3"/><path d="M26 29v-5h-5"/></svg>
    </div>
  </div>

  <section class="hero">
    <div class="ribbon">
      <svg width="560" height="110" viewBox="0 0 560 110">
        <path d="M0 34 H100 V82 H0 L26 58 Z" fill="#2b52e6"/>
        <path d="M560 34 H460 V82 H560 L534 58 Z" fill="#2b52e6"/>
        <rect x="70" y="8" width="420" height="94" rx="6" fill="#1a3fe0"/>
        <rect x="80" y="16" width="400" height="78" rx="4" fill="none" stroke="#fff" stroke-width="1.5" stroke-dasharray="5 4"/>
      </svg>
      <p class="ribbon-text">Get up to $5, 645* per year<br>in Grants if you qualify</p>
    </div>
    <h1 class="hero-title" style="font-weight:400">Complete our <strong>3 minute</strong> App!</h1>
  </section>

  <h2 class="interest-header" style="font-weight:400">SELECT AREA OF YOUR INTEREST</h2>

  <ul class="interest-list">
    <li class="interest-item">
      <span class="interest-icon"><svg width="40" height="40" viewBox="0 0 40 40" fill="none" stroke="#fff" stroke-width="2" stroke-linejoin="round"><path d="M34 5 L18 24 L21 27 Z"/><path d="M16 25c-5 0-7 4-8 10 5-1 10-3 11-7z"/></svg></span>
      <span class="interest-label">Art &amp; Design</span>
      <span class="interest-go"><svg width="18" height="18" viewBox="0 0 18 18" fill="none" stroke="#fff" stroke-width="3" stroke-linecap="round"><path d="M7 3l6 6-6 6"/></svg></span>
    </li>
    <li class="interest-item">
      <span class="interest-icon"><svg width="40" height="40" viewBox="0 0 40 40" fill="none" stroke="#fff" stroke-width="2"><rect x="5" y="12" width="30" height="21" rx="2"/><path d="M15 12V8h10v4M5 20h30M18 20v3h4v-3"/></svg></span>
      <span class="interest-label">Business</span>
      <span class="interest-go"><svg width="18" height="18" viewBox="0 0 18 18" fill="none" stroke="#fff" stroke-width="3" stroke-linecap="round"><path d="M7 3l6 6-6 6"/></svg></span>
    </li>
    <li class="interest-item">
      <span class="interest-icon"><svg width="40" height="40" viewBox="0 0 40 40" fill="none" stroke="#fff" stroke-width="2"><rect x="13" y="6" width="10" height="16" rx="2" transform="rotate(-45 18 14)"/><path d="M20 19L31 30M8 34h16"/></svg></span>
      <span class="interest-label">Criminal Justice</span>
      <span class="interest-go"><svg width="18" height="18" viewBox="0 0 18 18" fill="none" stroke="#fff" stroke-width="3" stroke-linecap="round"><path d="M7 3l6 6-6 6"/></svg></span>
    </li>
    <li class="interest-item">
      <span class="interest-icon"><svg width="46" height="40" viewBox="0 0 46 40"><g fill="#fff" font-family="Open Sans, sans-serif" font-size="14" text-anchor="middle"><text x="23" y="16">ABC</text><text x="23" y="35">1 2 3</text></g><path d="M6 21h34" stroke="#fff" stroke-width="1.5"/></svg></span>
      <span class="interest-label">Education &amp; Teaching</span>
      <span class="interest-go"><svg width="18" height="18" viewBox="0 0 18 18" fill="none" stroke="#fff" stroke-width="3" stroke-linecap="round"><path d="M7 3l6 6-6 6"/></svg></span>
    </li>
    <li class="interest-item">
      <span class="interest-icon"><svg width="40" height="40" viewBox="0 0 40 40" fill="none" stroke="#fff" stroke-width="2" stroke-linecap="round"><circle cx="20" cy="8" r="3"/><path d="M18 11L9 35M22 11l9 24M10 26h20"/></svg></span>
      <span class="interest-label">Engineering</span>
      <span class="interest-go"><svg width="18" height="18" viewBox="0 0 18 18" fill="none" stroke="#fff" stroke-width="3" stroke-linecap="round"><path d="M7 3l6 6-6 6"/></svg></span>
    </li>
    <li class="interest-item">
      <span class="interest-icon"><svg width="40" height="40" viewBox="0 0 40 40" fill="none" stroke="#fff" stroke-width="2" stroke-linejoin="round"><path d="M20 12c-4-3-9-3-14-2v20c5-1 10-1 14 2 4-3 9-3 14-2V10c-5-1-10-1-14 2zM20 12v20"/></svg></span>
      <span class="interest-label">Other</span>
      <span class="interest-go"><svg width="18" height="18" viewBox="0 0 18 18" fill="none" stroke="#fff" stroke-width="3" stroke-linecap="round"><path d="M7 3l6 6-6 6"/></svg></span>
    </li>
  </ul>
  <div class="list-foot"></div>

  <nav class="toolbar">
    <svg width="40" height="44" viewBox="0 0 40 44" fill="none" stroke="#fff" stroke-width="2.4" stroke-linecap="round"><path d="M27 6L11 22l16 16"/></svg>
    <svg width="40" height="44" viewBox="0 0 40 44" fill="none" stroke="#fff" stroke-width="2.4" stroke-linecap="round"><path d="M13 6l16 16-16 16"/></svg>
    <svg width="40" height="44" viewBox="0 0 40 44" fill="none" stroke="#fff" stroke-width="2"><path d="M14 14H7v26h26V14h-7"/><path d="M20 30V4M13 11l7-7 7 7"/></svg>
    <svg width="48" height="44" viewBox="0 0 48 44" fill="none" stroke="#fff" stroke-width="2"><path d="M6 6h16a2 2 0 0 1 2 2v30a2 2 0 0 0-2-2H6zM42 6H26a2 2 0 0 0-2 2v30a2 2 0 0 1 2-2h16z"/></svg>
    <svg width="44" height="44" viewBox="0 0 44 44" fill="none" stroke="#fff" stroke-width="2"><rect x="4" y="12" width="28" height="26"/><path d="M10 12V6h28v26h-6"/></svg>
  </nav>
</main>
</body>
</html>
```